Wordpress site for cyber security and network perfomance software vendor

We need a brand new Wordpress website consisting of a single home/landing page and page template so that we can add pages in future.
The website is intended to provide information to prospects and customers. The homepage should have a top menu bar that is customizable similar to what we already have at quillmarsh.com.
Note that we are after a new design – that is, please don’t reference our existing website for design inspiration (quillmarsh.com)
We are after a Wordpress site that may be implemented straight onto our Wordpress hoster (HostPetal) .
Quillmarsh is a software company delivering a solution for customers to get visibility of network performance and cyber security. The Quillmarsh solution reduces cyber security risk, identifies performance bottlenecks and ultimately lower costs by reducing the number of tools need to monitor the IT environment
We deliver network performance and cyber security information to the IT manager and network teams in a format that they understand, at a realistic cost, and requiring minimal resource to implement. This is a crowded market, most competitors provide highly complex, expensive and highly customized tools to large enterprise. Quillmarsh makes this style of visibility tool accessible to the mid market.

Target Market(s)

IT Managers, network engineers, mid market organisations, IT service providers

Industry/Entity Type

IT

Font styles to use
Sans Serif

Colors
0094D4
00A9DD
6FCCEA
C7EBF8
E9F6FB

Requirements
Must have
• Fully coded for WordPress. Responsive and mobile friendly. The website copy is provided in the attached document. Utilise the Quillmarsh logo colors as part of the design (Dark Blue: 2E4F99, Light Blue: 00AFF4, Green: 73D94F). Top Horizontal menu bar for additional pages. Implement one of our screenshots (I have included a bunch of screenshots to choose from)
Nice to have
• Icons, panels or infographics matching the services. Our existing site is built using Divi – this is not a requirement for the new site but a nice to have as we are familiar with Divi.
Should not have
• Preferably no corporate images – business people shaking hands or teams of people a meeting room (or that kind of thing)

```html
<!DOCTYPE html>
<html lang="en">
<head>
<meta charset="utf-8">
<title>Quillmarsh — Network Performance &amp; Cyber Security</title>
<link href="https://fonts.googleapis.com/css2?family=Fira+Sans:wght@400;500;600&family=Lato:wght@400;700&display=swap" rel="stylesheet">
<style>
:root{
  --blue:#0094D4;
  --blue-bright:#00A9DD;
  --blue-soft:#6FCCEA;
  --blue-pale:#C7EBF8;
  --blue-wash:#E9F6FB;
  --brand-dark:#2E4F99;
  --brand-light:#00AFF4;
  --green:#73D94F;
  --green-link:#5CC23A;
  --ink:#111111;
  --text:#333333;
  --footer:#000000;
}
*{box-sizing:border-box;margin:0;padding:0}
html,body{width:1200px;height:3396px;overflow:hidden}
body{position:relative;background:#fff;font-family:"Lato",sans-serif;color:var(--text)}
.heading{font-family:"Fira Sans",sans-serif;font-weight:500;color:var(--ink)}
.btn{position:absolute;display:flex;align-items:center;justify-content:center;background:var(--blue);color:#fff;font-family:"Lato",sans-serif;font-weight:700;font-size:15px;letter-spacing:.3px;border-radius:22px;text-decoration:none}

/* header */
.site-header{position:absolute;left:0;top:0;width:1200px;height:84px;background:#fff}
.brand{position:absolute;display:flex;align-items:center;gap:10px;font-family:"Fira Sans",sans-serif;font-weight:400;color:var(--brand-dark);text-decoration:none}
.brand-dot{border-radius:50%;background:var(--green)}
.site-header .brand{left:112px;top:18px;font-size:34px}
.site-header .brand-dot{width:40px;height:40px}
.main-nav a{position:absolute;top:32px;font-family:"Lato",sans-serif;font-weight:700;font-size:15px;color:#1a1a1a;text-decoration:none}
.main-nav a.active{color:var(--green-link)}
.main-nav a.active::after{content:"";position:absolute;left:0;right:0;top:50px;height:3px;background:var(--green)}
.site-header .btn{left:945px;top:21px;width:144px;height:40px}

/* hero */
.hero{position:absolute;left:0;top:84px;width:1200px;height:641px;background:linear-gradient(100deg,#020a22 0%,#061a44 45%,#082a60 100%);overflow:hidden}
.hero-network{position:absolute;left:560px;top:0;width:640px;height:600px;background:radial-gradient(ellipse at 55% 50%,rgba(40,150,230,.55) 0%,rgba(20,90,180,.35) 35%,rgba(6,30,80,0) 70%)}
.hero h1{position:absolute;left:110px;top:150px;width:460px;font-family:"Fira Sans",sans-serif;font-weight:500;font-size:42px;line-height:52px;color:#fff}
.hero p{position:absolute;left:111px;top:268px;width:380px;font-size:16px;line-height:30px;color:#fff}
.hero .btn{left:111px;top:350px;width:145px;height:41px}
.hero svg{position:absolute;left:0;top:0}

/* why */
.why-photo{position:absolute;border-radius:12px}
.why-photo.code{left:111px;top:815px;width:426px;height:281px;background:linear-gradient(120deg,#1a2a6a 0%,#0a0f2a 45%,#2a1030 70%,#0c2050 100%)}
.why-photo.laptop{left:336px;top:964px;width:264px;height:326px;background:linear-gradient(150deg,#d8dcdf 0%,#9aa3a8 40%,#4a5156 75%,#2b3034 100%)}
.why h2{position:absolute;left:642px;top:842px;font-size:34px}
.why p{position:absolute;left:649px;top:913px;width:445px;font-size:15.5px;line-height:30.2px;color:#2a2a2a}
.why .btn{left:650px;top:1214px;width:144px;height:41px}

/* services */
.services{position:absolute;left:0;top:1378px;width:1200px;height:551px;background:var(--blue-wash)}
.services h2{position:absolute;left:0;top:76px;width:1200px;text-align:center;font-size:34px}
.service-card{position:absolute;top:166px;width:233px;height:293px;background:#fff;border-radius:12px;box-shadow:0 2px 10px rgba(0,60,100,.10);text-align:center}
.service-card svg{position:absolute;left:77px;top:16px}
.service-card h3{position:absolute;left:22px;right:22px;top:120px;font-family:"Fira Sans",sans-serif;font-weight:500;font-size:20px;line-height:30px;color:var(--ink)}
.service-card p{position:absolute;left:28px;right:28px;top:190px;font-size:15px;line-height:30px;color:#333}
.service-card.short p{top:160px}
.service-card .more{position:absolute;left:0;right:0;top:258px;font-family:"Fira Sans",sans-serif;font-weight:500;font-size:15px;color:var(--green-link)}
.carousel-arrow{position:absolute;top:304px;font-size:22px;color:#111;font-family:"Lato",sans-serif}

/* specialising */
.special h2{position:absolute;left:100px;top:2006px;width:1000px;text-align:center;font-size:37px;line-height:43px}
.dashboard{position:absolute;left:208px;top:2122px;width:784px;height:411px;background:linear-gradient(180deg,#141619 0%,#1c1e22 20%,#202329 100%);box-shadow:0 2px 10px rgba(0,0,0,.35)}
.special p{position:absolute;left:170px;top:2566px;width:860px;text-align:center;font-size:15.5px;line-height:30.2px;color:#2a2a2a}
.special .btn{left:529px;top:2747px;width:143px;height:41px}

/* footer */
.site-footer{position:absolute;left:0;top:2870px;width:1200px;height:526px}
.site-footer svg.wave{position:absolute;left:0;top:0}
.site-footer .brand{left:112px;top:167px;font-size:44px;color:var(--brand-light)}
.site-footer .brand-dot{width:56px;height:56px;background:var(--brand-light)}
.footer-about{position:absolute;left:114px;top:280px;width:280px;font-size:15px;line-height:26px;color:#fff}
.footer-col h4{position:absolute;top:138px;font-family:"Lato",sans-serif;font-weight:700;font-size:16px;color:#fff}
.footer-col h4::after{content:"";position:absolute;left:0;top:29px;width:36px;height:3px;background:var(--green)}
.footer-col ul{position:absolute;list-style:none;top:182px}
.footer-col li{font-size:15.5px;line-height:30.1px;color:#fff}
.contact li{display:flex;align-items:center;gap:8px;line-height:37px}
.social{position:absolute;left:964px;top:182px;display:flex;gap:9px}
.social span{width:34px;height:34px;border-radius:50%;display:block}
.social .s1{background:#1877d9}.social .s2{background:#3bb54a}.social .s3{background:#2e9c3a}
.footer-rule{position:absolute;left:111px;top:416px;width:978px;height:1px;background:#333}
.copyright{position:absolute;left:0;top:462px;width:1200px;text-align:center;font-size:15px;color:#fff}
.sr{position:absolute;width:1px;height:1px;overflow:hidden;clip:rect(0 0 0 0)}
</style>
</head>
<body>

<header class="site-header">
  <a class="brand" href="#"><span class="brand-dot"></span>quillmarsh</a>
  <nav class="main-nav">
    <a href="#" class="active" style="left:382px">HOME</a>
    <a href="#" style="left:475px">PRODUCT</a>
    <a href="#" style="left:595px">BLOG</a>
    <a href="#" style="left:682px">ABOUT</a>
    <a href="#" style="left:781px">PARTNER PORTAL</a>
  </nav>
  <a class="btn" href="#">DEMO LOGIN</a>
</header>

<section class="hero">
  <div class="hero-network" role="img" aria-label="Glowing blue network of connected points over a dark background"></div>
  <h1>Quillmarsh is a Software Company</h1>
  <p>Lorem ipsum dolor sit amet, consectetur adipiscing elit, sed do eiusmod tempor</p>
  <a class="btn" href="#">LEARN MORE</a>
  <svg width="1200" height="641" viewBox="0 0 1200 641" aria-hidden="true">
    <path d="M0,489 C280,610 620,665 1200,582 L1200,641 L0,641 Z" fill="var(--blue)"/>
    <path d="M0,562 C300,650 700,660 1200,597 L1200,641 L0,641 Z" fill="#fff"/>
  </svg>
</section>

<section class="why">
  <div class="why-photo code" role="img" aria-label="Close-up of colourful source code on a dark screen"></div>
  <div class="why-photo laptop" role="img" aria-label="Hands typing on a laptop keyboard with network icons overlaid"></div>
  <h2 class="heading">Why Quillmarsh?</h2>
  <p>At Quillmarsh, we understand the challenges that you face. Cyber security and network incidents can have devastating impacts on small to medium organisations because you typically don’t have the time, staff, or resources to develop complicated responses to cyber security threats.That’s why small to medium sized organisations are vulnerable to potentially devastating cyber incidents Did you know that on average, it took over 220 days for organisations to identify a breach and a further 80 days to contain the breach?</p>
  <a class="btn" href="#">LEARN MORE</a>
</section>

<section class="services">
  <h2 class="heading">We deliver everything you need</h2>
  <span class="carousel-arrow" style="left:42px">‹</span>
  <span class="carousel-arrow" style="left:1134px">›</span>

  <article class="service-card" style="left:112px">
    <svg width="80" height="86" viewBox="0 0 80 86" fill="none" stroke="var(--blue-bright)" stroke-width="2.5">
      <rect x="4" y="56" width="10" height="26"/><rect x="20" y="44" width="10" height="38"/><rect x="36" y="50" width="10" height="32"/><rect x="52" y="34" width="10" height="48"/><rect x="66" y="18" width="10" height="64"/>
      <polyline points="9,40 25,28 41,34 57,18 71,6" stroke="var(--green)"/>
      <circle cx="9" cy="40" r="3" stroke="var(--green)"/><circle cx="25" cy="28" r="3" stroke="var(--green)"/><circle cx="41" cy="34" r="3" stroke="var(--green)"/><circle cx="57" cy="18" r="3" stroke="var(--green)"/><circle cx="71" cy="6" r="3" stroke="var(--green)"/>
    </svg>
    <h3>Sophisticated Data Analytics</h3>
    <p>Powerful data analytics correlate threat data</p>
    <span class="more">Learn More ➔</span>
  </article>

  <article class="service-card" style="left:360px">
    <svg width="96" height="70" viewBox="0 0 96 70" fill="none" stroke="var(--blue-bright)" stroke-width="2.5" style="left:68px;top:20px">
      <rect x="3" y="8" width="88" height="52" rx="3"/>
      <rect x="10" y="20" width="7" height="20"/><rect x="21" y="28" width="7" height="12"/><rect x="32" y="16" width="7" height="24"/>
      <circle cx="28" cy="48" r="10" stroke="var(--green)"/>
      <line x1="48" y1="46" x2="84" y2="46"/><line x1="48" y1="52" x2="76" y2="52"/>
      <polyline points="48,36 60,24 70,30 84,14" stroke="var(--green)"/>
      <circle cx="84" cy="8" r="6"/>
    </svg>
    <h3 style="left:50px;right:50px">Best Visual Analytics</h3>
    <p>Proactive alerts and dynamic traffic flows are</p>
    <span class="more">Learn More ➔</span>
  </article>

  <article class="service-card short" style="left:608px">
    <svg width="80" height="80" viewBox="0 0 80 80" fill="none" stroke="var(--blue-bright)" stroke-width="2.5">
      <path d="M6,6 H30 V16 A5,5 0 0 1 30,26 V34 H6 Z"/>
      <path d="M46,6 H74 V34 H64 A5,5 0 0 0 54,34 H46 Z"/>
      <path d="M6,46 H16 A5,5 0 0 0 26,46 H34 V74 H6 Z"/>
      <path d="M46,46 H74 V74 H46 V64 A5,5 0 0 0 46,54 Z"/>
      <circle cx="40" cy="40" r="11" stroke="var(--green)" fill="#fff"/>
      <circle cx="40" cy="40" r="4" stroke="var(--green)"/>
    </svg>
    <h3>Flexible Solutions</h3>
    <p>Our network monitoring AND cyber security solution can be scaled</p>
    <span class="more">Learn More ➔</span>
  </article>

  <article class="service-card short" style="left:856px">
    <svg width="80" height="80" viewBox="0 0 80 80" fill="none" stroke-width="4">
      <path d="M12,28 A30,30 0 0 1 62,14" stroke="var(--green)"/>
      <path d="M68,52 A30,30 0 0 1 18,66" stroke="var(--green)"/>
      <path d="M56,8 L64,16 L54,20" stroke="var(--green)"/>
      <path d="M24,72 L16,64 L26,60" stroke="var(--green)"/>
      <text x="22" y="50" font-family="Fira Sans, sans-serif" font-weight="600" font-size="28" fill="var(--blue-bright)" stroke="none">24</text>
      <text x="58" y="32" font-family="Fira Sans, sans-serif" font-size="11" fill="var(--blue-bright)" stroke="none">h</text>
    </svg>
    <h3>Superior Service</h3>
    <p style="left:24px;right:24px">From first contact through to deployment, our friendly, expert team</p>
    <span class="more">Learn More ➔</span>
  </article>
</section>

<section class="special">
  <h2 class="heading">Specialising in IT Network Performance and Cyber Security Solutions for Small to Medium Organisations.</h2>
  <div class="dashboard" role="img" aria-label="Product screenshot: dark network performance overview dashboard with latency chart and top performing apps and hosts"></div>
  <p>Specialising in IT Network Performance and Cyber Security Solutions for Small to Medium Organisations.<br>Perhaps you’ve outsourced your IT support and have discovered that your service provider doesn’t have visibility of your network?&nbsp; It’s not easy being an IT manager. Especially if you work in a small to medium sized organisation. You’re typically stretched to the limit with an understaffed team and there’s simply not enough hours in the day to tackle all the increasing demands</p>
  <a class="btn" href="#">LEARN MORE</a>
</section>

<footer class="site-footer">
  <svg class="wave" width="1200" height="526" viewBox="0 0 1200 526" aria-hidden="true">
    <path d="M0,117 C300,10 800,-12 1200,71 L1200,526 L0,526 Z" fill="var(--blue)"/>
    <path d="M0,176 C300,40 800,22 1200,86 L1200,526 L0,526 Z" fill="var(--footer)"/>
  </svg>
  <a class="brand" href="#"><span class="brand-dot"></span>quillmarsh</a>
  <p class="footer-about">Lorem ipsum dolor sit amet, consectetur adipiscing elit, sed do eiusmod tempor incididunt ut</p>

  <div class="footer-col">
    <h4 style="left:466px">QUICK LINK</h4>
    <ul style="left:469px"><li>Home</li><li>Product</li><li>Blog</li><li>About</li><li>Partner Portal</li><li>Demo Login</li></ul>
  </div>
  <div class="footer-col contact">
    <h4 style="left:701px">CONTACT</h4>
    <ul style="left:702px;top:172px">
      <li><svg width="12" height="14" viewBox="0 0 12 14"><path d="M6,0 A5,5 0 0 1 11,5 C11,9 6,14 6,14 C6,14 1,9 1,5 A5,5 0 0 1 6,0 Z" fill="var(--green)"/><circle cx="6" cy="5" r="2" fill="#000"/></svg>Quillmarsh Australia</li>
      <li><svg width="13" height="13" viewBox="0 0 13 13"><path d="M2,0 L5,3 L3.5,5 C4.5,7 6,8.5 8,9.5 L10,8 L13,11 L11,13 C5,12.5 0.5,8 0,2 Z" fill="var(--green)"/></svg>61 2 5550 0142</li>
      <li><svg width="14" height="11" viewBox="0 0 14 11"><rect width="14" height="11" rx="1" fill="var(--green)"/><polyline points="1,1 7,6 13,1" fill="none" stroke="#000" stroke-width="1.3"/></svg>hello@quillmarsh.com</li>
    </ul>
  </div>
  <div class="footer-col">
    <h4 style="left:966px">FOLLOW US</h4>
  </div>
  <div class="social">
    <span class="s1"><span class="sr">Social profile one</span></span>
    <span class="s2"><span class="sr">Social profile two</span></span>
    <span class="s3"><span class="sr">Video channel</span></span>
  </div>

  <div class="footer-rule"></div>
  <p class="copyright">© 2021 quillmarsh All Rights Reserved</p>
</footer>

</body>
</html>
```